Chimney Service company needs new business card design

We need a updated business card with our new logo added. We provide a full range of chimney services throughout Vermont and New Hampshire. The business card will be one sided and color. Attached is our current business card another document showing all the information we would like on the card.
We dont like a lot of flashy colors.... here is a link to our website to get an idea of our branding www.flueguardianvt.example

Target Market(s)

homeowners

Industry/Entity Type

Business

Contact Information for Business Card

See attached sheet for content.

Font styles to use
Serif
Sans Serif

Requirements
Must have
• all information provided on separate sheet
Should not have
• Additional information that may clogg up design

```html
<!DOCTYPE html>
<html lang="en">
<head>
<meta charset="utf-8">
<title>Flue Guardian – Business Card</title>
<link rel="stylesheet" href="https://fonts.googleapis.com/css2?family=Bebas+Neue&family=Cinzel:wght@400&family=Roboto:wght@400&display=swap">
<style>
  :root {
    --page-bg: #2b2b2b;
    --card-bg: #f3f3f3;
    --ink: #2f2f2f;
    --ink-soft: #4a4a4a;
    --accent: #9b1b1b;
    --band: #363636;
    --band-text: #ececec;
  }
  * { margin: 0; padding: 0; box-sizing: border-box; }
  html, body {
    width: 1200px; height: 871px; overflow: hidden;
    background: var(--page-bg);
  }
  .card {
    position: absolute;
    left: 80px; top: 140px;
    width: 1040px; height: 592px;
    background: var(--card-bg);
    overflow: hidden;
  }
  .brand-mark {
    position: absolute;
    left: 218px; top: 100px;
    width: 76px; height: 76px;
    background: var(--ink);
  }
  .brand-name {
    position: absolute;
    left: 40px; top: 238px;
    width: 436px;
    text-align: center;
    font-family: "Cinzel", serif;
    font-weight: 400;
    font-size: 40px;
    letter-spacing: 1px;
    color: var(--ink);
  }
  .divider {
    position: absolute;
    left: 240px; top: 294px;
    width: 747px; height: 2px;
    background: var(--ink);
  }
  .highlights {
    position: absolute;
    right: 53px; top: 64px;
    list-style: none;
    text-align: right;
    font-family: "Bebas Neue", sans-serif;
    font-size: 31px;
    line-height: 35px;
    color: var(--ink);
  }
  .contact {
    position: absolute;
    right: 53px; top: 196px;
    list-style: none;
    font-family: "Roboto", sans-serif;
    font-size: 25px;
    line-height: 34px;
    color: var(--ink-soft);
  }
  .contact li {
    display: flex; align-items: center; justify-content: flex-end; gap: 12px;
  }
  .contact svg { width: 20px; height: 20px; fill: var(--accent); }
  .services {
    position: absolute;
    left: 66px; top: 354px;
    list-style: none;
    font-family: "Roboto", sans-serif;
    font-size: 25px;
    line-height: 31.5px;
    color: var(--ink-soft);
  }
  .services li { position: relative; padding-left: 31px; }
  .services li::before {
    content: "";
    position: absolute; left: 0; top: 12px;
    width: 7px; height: 7px; border-radius: 50%;
    background: var(--accent);
  }
  .footer-band {
    position: absolute;
    left: 0; bottom: 0;
    width: 100%; height: 50px;
    background: var(--band);
  }
  .website {
    position: absolute;
    left: 60px; top: 11px;
    font-family: "Roboto", sans-serif;
    font-size: 24px;
    letter-spacing: 3.5px;
    color: var(--band-text);
  }
</style>
</head>
<body>
  <main class="card">
    <div class="brand-mark"></div>
    <div class="brand-name">FLUE GUARDIAN</div>
    <div class="divider"></div>

    <ul class="highlights">
      <li>Serving VT &amp; New Hampshire since 1994</li>
      <li>Fully insured — free estimates</li>
      <li>Family owned &amp; operated</li>
    </ul>

    <ul class="contact">
      <li>802-555-0147
        <svg viewBox="0 0 24 24" aria-hidden="true"><path d="M6.6 10.8a15.2 15.2 0 0 0 6.6 6.6l2.2-2.2a1 1 0 0 1 1-.25 11.4 11.4 0 0 0 3.6.57 1 1 0 0 1 1 1V20a1 1 0 0 1-1 1A17 17 0 0 1 3 4a1 1 0 0 1 1-1h3.5a1 1 0 0 1 1 1c0 1.25.2 2.45.57 3.57a1 1 0 0 1-.25 1z"/></svg>
      </li>
      <li>info@flueguardianvt.example
        <svg viewBox="0 0 24 24" aria-hidden="true"><path d="M2 5h20v14H2z"/><path d="M3 6l9 6.3L21 6" fill="none" stroke="#f3f3f3" stroke-width="1.6"/></svg>
      </li>
    </ul>

    <ul class="services">
      <li>Full Masonry Services</li>
      <li>Historic chimney restoration</li>
      <li>Stainless steel liners</li>
      <li>New Chimney installations</li>
      <li>HFSA Certified Chimney sweeps</li>
    </ul>

    <div class="footer-band">
      <span class="website">www.flueguardianvt.example</span>
    </div>
  </main>
</body>
</html>
```